Website design and coding for new consultancy company

I need to have a full website designed for a new consultancy business I'm trying to establish. It's called BrightPath consult. I need an English version to begin with, and then there should be a Danish version as well, but I'll translate that myself. Just be aware that I need two language versions. The consultancy field that I'm targeting is Leadership - and specialist development. I offer to facilitate corporate academies for global companies as well as specific workshops within leadership- or team development, strategy sessions, personal coaching and facilitation of D&I (Diversity and inclusion) workshops. BTW my logo is not in high resolution - I need that as well.

Target Market(s)

Larger companies that has a need for developing their inhouse leadership capabilities or that wants to develop their specialists to take on more responsibility.

Industry/Entity Type

Consultancy business

Coding

Coded - Design and coding required

Number of Pages Required

5+ page

Requirements
Must have
• Introduction site with a catch phrase. Book a meeting. Services that's beeing offered. Blog site with white papers etc. Language toggle (Danish/English). Cases/testimonials. About site. Contact site.

```html
<!DOCTYPE html>
<html lang="en">
<head>
<meta charset="utf-8">
<title>BrightPath consult</title>
<link rel="alternate" hreflang="en" href="/en/">
<link rel="alternate" hreflang="da" href="/da/">
<link rel="stylesheet" href="https://fonts.googleapis.com/css2?family=League+Gothic&family=Montserrat:wght@400;500;600;700&display=swap">
<style>
:root{
  --blue:#1f7fcc;
  --ink:#0d0d0d;
  --text:#333;
  --muted:#6b6b6b;
  --field:#eef4fb;
  --field-line:#d9e4f0;
  --white:#fff;
  --footer:#0a0a0a;
}
*{box-sizing:border-box;margin:0;padding:0}
html,body{width:1200px;height:2635px;overflow:hidden}
body{position:relative;background:var(--white);font-family:"Montserrat",sans-serif;color:var(--text)}
a{color:inherit;text-decoration:none}
.abs{position:absolute}
.display{font-family:"League Gothic",sans-serif;font-weight:400;color:var(--ink);text-transform:uppercase;letter-spacing:1px;line-height:1}
.skew-btn{position:absolute;display:flex;align-items:center;justify-content:center;font-weight:700;font-size:16px;letter-spacing:.3px;color:var(--white);background:var(--blue);clip-path:polygon(5% 0,100% 0,95% 100%,0 100%);text-transform:uppercase}
.rule{position:absolute;height:3px;width:72px;background:var(--blue)}

/* header */
.site-header{position:absolute;top:0;left:0;width:1200px;height:74px;border-top:3px solid var(--blue);border-bottom:1px solid #e6e6e6;background:var(--white);z-index:5}
.brand{position:absolute;left:146px;top:16px;display:flex;align-items:center;gap:10px}
.brand-mark{width:14px;height:14px;background:var(--blue)}
.brand-name{font-family:"League Gothic",sans-serif;font-size:44px;line-height:1;letter-spacing:1px;color:var(--ink)}
.nav{position:absolute;left:451px;top:27px;display:flex;gap:33px;font-size:15px;color:var(--ink)}
.nav .active{color:var(--blue)}
.quote-btn{left:904px;top:12px;width:152px;height:44px;font-size:15px}

/* hero */
.hero{position:absolute;top:74px;left:0;width:1200px;height:596px;clip-path:polygon(0 0,100% 0,100% 519px,0 100%);background:linear-gradient(90deg,#e4e8ea 0%,#dde3e5 35%,#c9cfd0 55%,#a8a8a6 75%,#8f8c88 100%)}
.hero-photo{position:absolute;left:480px;top:0;width:720px;height:596px;background:radial-gradient(ellipse at 60% 45%,#b59a86 0%,#8b7a70 35%,#6d6e70 60%,rgba(200,205,207,0) 85%)}
.hero-fade{position:absolute;left:0;top:0;width:700px;height:596px;background:linear-gradient(90deg,rgba(232,236,238,.95) 55%,rgba(232,236,238,0))}
.eyebrow{left:144px;top:177px;font-size:15px;color:var(--blue);text-transform:uppercase}
.hero-title{left:142px;top:208px;font-size:66px;line-height:72px}
.hero-lead{left:144px;top:357px;width:390px;font-size:18.5px;line-height:29px;color:var(--ink)}
.start-btn{left:146px;top:443px;width:182px;height:48px;font-size:17px}

/* services */
.section-title{left:0;width:1200px;text-align:center;font-size:54px}
.services-title{top:706px}
.services-rule{left:564px;top:766px}
.slider-arrow{position:absolute;width:37px;height:37px;border-radius:50%;display:flex;align-items:center;justify-content:center}
.arrow-prev{left:68px;top:952px;background:#e7f1fb}
.arrow-next{left:1095px;top:952px;background:var(--blue)}
.service-card{position:absolute;top:806px;width:296px;height:328px;background:var(--white);box-shadow:0 2px 14px rgba(0,0,0,.08);text-align:center}
.service-card svg.icon{margin-top:32px}
.service-name{margin-top:18px;font-size:17px;font-weight:500;color:var(--ink)}
.service-text{margin:12px auto 0;width:250px;font-size:14px;line-height:23px;color:var(--muted)}
.read-more{position:absolute;left:82px;top:260px;display:flex;align-items:center;gap:8px;font-weight:700;font-size:15px;color:var(--blue)}
.read-more .tag{width:34px;height:34px;background:var(--blue);clip-path:polygon(18% 0,100% 0,82% 100%,0 100%);display:flex;align-items:center;justify-content:center}

/* about */
.about{position:absolute;top:1187px;left:0;width:1200px;height:578px;background:linear-gradient(180deg,#2585d2,#1d78c4);clip-path:polygon(0 20px,100% 76px,100% 525px,0 100%)}
.about-photo{position:absolute;left:786px;top:1190px;width:414px;height:540px;background:linear-gradient(180deg,#b08a68 0%,#2a5f93 35%,#27446b 70%,#9fb9d2 100%);clip-path:polygon(25% 0,75% 0,100% 12%,100% 96%,0 100%,0 45%)}
.about-title{left:144px;top:1286px;font-size:54px;color:var(--white)}
.about-rule{left:144px;top:1351px;background:var(--white)}
.about-copy{left:144px;top:1375px;width:512px;font-size:14.2px;line-height:23.2px;color:var(--white)}
.about-copy p+p{margin-top:4px}
.about-btn{left:146px;top:1645px;width:151px;height:44px;background:var(--white);color:var(--blue);font-size:15px}

/* contact */
.contact-title{top:1818px}
.contact-rule{left:564px;top:1882px}
.field{position:absolute;height:46px;background:var(--field);border:1px solid var(--field-line);display:flex;align-items:center;gap:7px;padding-left:18px;font-size:13.5px;color:#777}
.field.message{align-items:flex-start;padding-top:14px}
.submit-btn{left:517px;top:2204px;width:167px;height:44px;font-size:15px}

/* footer */
.site-footer{position:absolute;top:2286px;left:0;width:1200px;height:349px;background:var(--footer);clip-path:polygon(0 0,100% 77px,100% 100%,0 100%)}
.footer-brand{left:141px;top:2430px}
.footer-brand .brand-mark{background:var(--white)}
.footer-brand .brand-name{color:var(--white);font-size:48px}
.socials{left:178px;top:2500px;display:flex;gap:10px}
.social{width:26px;height:26px;border:1.5px solid var(--white);border-radius:50%}
.social.on{background:var(--blue);border-color:var(--blue)}
.foot-col{top:2395px;color:var(--white);font-size:14.5px}
.foot-col h4{font-weight:500;font-size:16.5px;color:var(--blue);text-transform:uppercase;margin-bottom:12px}
.foot-col li{list-style:none;line-height:25.6px;padding-left:2px}
.contact-line{display:flex;align-items:center;gap:9px;line-height:30px}
.foot-divider{left:144px;top:2585px;width:912px;height:1px;background:#333}
.copyright{left:0;top:2601px;width:1200px;text-align:center;color:var(--white);font-size:14.5px}
</style>
</head>
<body>

<header class="site-header">
  <a class="brand" href="/en/"><span class="brand-mark"></span><span class="brand-name">BRIGHTPATH</span></a>
  <nav class="nav"><a class="active" href="/en/">HOME</a><a href="/en/about">ABOUT</a><a href="/en/services">SERVICES</a><a href="/en/blog">BLOG</a><a href="#contact">CONTACT</a></nav>
  <a class="skew-btn quote-btn" href="#contact">Get a Quote</a>
</header>

<section class="hero">
  <div class="hero-photo" role="img" aria-label="Photo of a business team gathered around a laptop in a bright office"></div>
  <div class="hero-fade"></div>
</section>
<div class="abs eyebrow">Welcome to BrightPath consult</div>
<h1 class="abs display hero-title">Empowering leaders.<br>Elevating teams.</h1>
<p class="abs hero-lead">Lorem ipsum dolor sit amet, consectetur adipiscing elit, sed do eiusmod.</p>
<a class="skew-btn start-btn" href="#contact">Get Started</a>

<h2 class="abs display section-title services-title">BrightPath consult services</h2>
<div class="rule services-rule"></div>

<div class="slider-arrow arrow-prev"><svg width="16" height="12" viewBox="0 0 16 12"><path d="M15 6H2M6 1 1 6l5 5" fill="none" stroke="#222" stroke-width="1.6"/></svg></div>
<div class="slider-arrow arrow-next"><svg width="16" height="12" viewBox="0 0 16 12"><path d="M1 6h13M10 1l5 5-5 5" fill="none" stroke="#fff" stroke-width="1.6"/></svg></div>

<article class="service-card" style="left:146px">
  <svg class="icon" width="90" height="90" viewBox="0 0 90 90" fill="none" stroke="#1f7fcc" stroke-width="2.5"><rect x="18" y="8" width="40" height="78"/><rect x="4" y="50" width="14" height="36"/><path d="M58 36h12l16 14v36H58"/><path d="M26 20h8M42 20h8M26 32h8M42 32h8M26 44h8M42 44h8M26 56h8M42 56h8M26 68h8M42 68h8M64 50h14M64 60h16M64 70h16"/></svg>
  <div class="service-name">Corporate Academies</div>
  <p class="service-text">Lorem ipsum dolor sit amet, consectetur adipiscing elit, sed do eiusmod tempor.</p>
  <div class="read-more"><span class="tag"><svg width="14" height="14" viewBox="0 0 14 14"><path d="M2 12 12 2M4 2h8v8" fill="none" stroke="#fff" stroke-width="1.8"/></svg></span>READ MORE</div>
</article>

<article class="service-card" style="left:452px">
  <svg class="icon" width="90" height="90" viewBox="0 0 90 90" fill="none" stroke="#1f7fcc" stroke-width="2.5"><circle cx="16" cy="14" r="8"/><circle cx="74" cy="14" r="8"/><rect x="32" y="4" width="26" height="18" rx="2"/><path d="M38 11h14M38 16h10M6 86V40q0-10 10-10h6l14 12M84 86V40q0-10-10-10h-6L54 42M20 86V58M70 86V58M30 60h30"/></svg>
  <div class="service-name">Personal Coaching</div>
  <p class="service-text">Lorem ipsum dolor sit amet, consectetur adipiscing elit, sed do eiusmod tempor.</p>
  <div class="read-more"><span class="tag"><svg width="14" height="14" viewBox="0 0 14 14"><path d="M2 12 12 2M4 2h8v8" fill="none" stroke="#fff" stroke-width="1.8"/></svg></span>READ MORE</div>
</article>

<article class="service-card" style="left:759px">
  <svg class="icon" width="90" height="90" viewBox="0 0 90 90" fill="none" stroke="#1f7fcc" stroke-width="2.5"><circle cx="45" cy="45" r="28"/><rect x="6" y="6" width="22" height="22" rx="6"/><rect x="62" y="6" width="22" height="22" rx="6"/><rect x="6" y="62" width="22" height="22" rx="6"/><rect x="62" y="62" width="22" height="22" rx="6"/><path d="M38 38l14 14M52 38 38 52"/></svg>
  <div class="service-name">Inclusion Workshops</div>
  <p class="service-text">Lorem ipsum dolor sit amet, consectetur adipiscing elit, sed do eiusmod tempor.</p>
  <div class="read-more"><span class="tag"><svg width="14" height="14" viewBox="0 0 14 14"><path d="M2 12 12 2M4 2h8v8" fill="none" stroke="#fff" stroke-width="1.8"/></svg></span>READ MORE</div>
</article>

<section class="about" role="img" aria-label="Blue band over a faint city skyline"></section>
<div class="about-photo" role="img" aria-label="Portrait of the consultant in a navy suit"></div>
<h2 class="abs display about-title">About BrightPath consult</h2>
<div class="rule about-rule"></div>
<div class="abs about-copy">
  <p>Lorem ipsum dolor sit amet, consectetur adipiscing elit, sed do eiusmod tempor incididunt ut labore et dolore magna aliqua. Ut enim ad minim veniam, quis nostrud exercitation ullamco laboris nisi ut aliquip ex ea commodo consequat.</p>
  <p>Duis aute irure dolor in reprehenderit in voluptate velit esse cillum dolore eu fugiat nulla pariatur. Excepteur sint occaecat cupidatat non proident, sunt in culpa qui officia deserunt mollit anim id estlaborum.accusantium doloremque laudantium, totam ex ea commodo consequat. eaque ipsa quae ab illo inventore veritatis et quasi architecto beatae vitae dicta sunt explicabo non proident, sunt in culpa qui officia.</p>
</div>
<a class="skew-btn about-btn" href="/en/about">Read More</a>

<h2 class="abs display section-title contact-title" id="contact">Contact us</h2>
<div class="rule contact-rule"></div>

<div class="field" style="left:181px;top:1922px;width:409px"><svg width="12" height="13" viewBox="0 0 12 13" fill="none" stroke="#888" stroke-width="1.2"><circle cx="6" cy="4" r="3"/><path d="M1 12q0-5 5-5t5 5z"/></svg>First Name*</div>
<div class="field" style="left:611px;top:1922px;width:409px"><svg width="12" height="13" viewBox="0 0 12 13" fill="none" stroke="#888" stroke-width="1.2"><circle cx="6" cy="4" r="3"/><path d="M1 12q0-5 5-5t5 5z"/></svg>Last Name*</div>
<div class="field" style="left:181px;top:1992px;width:409px"><svg width="13" height="10" viewBox="0 0 13 10"><rect width="13" height="10" rx="1" fill="#777"/><path d="M0 1l6.5 5L13 1" fill="none" stroke="#eef4fb" stroke-width="1.2"/></svg>Email Address*</div>
<div class="field" style="left:611px;top:1992px;width:409px"><svg width="11" height="11" viewBox="0 0 11 11"><path d="M2 0l2 3-1 1.5q1 2 3 3L7.5 6.5l3 2L9 11Q1 9 0 2z" fill="#777"/></svg>Phone Number*</div>
<div class="field message" style="left:181px;top:2061px;width:837px;height:104px"><svg width="13" height="11" viewBox="0 0 13 11"><ellipse cx="6.5" cy="5" rx="6.5" ry="4.5" fill="#777"/><path d="M2 8l-1 3 4-2z" fill="#777"/></svg>Message*</div>
<div class="skew-btn submit-btn">Submit Now</div>

<footer class="site-footer"></footer>
<div class="abs brand footer-brand"><span class="brand-mark"></span><span class="brand-name">BRIGHTPATH</span></div>
<div class="abs socials"><span class="social"></span><span class="social"></span><span class="social on"></span><span class="social"></span></div>

<div class="abs foot-col" style="left:418px"><h4>Information</h4><ul><li>Home</li><li>About Us</li><li>services</li><li>Blog</li><li>Contact Us</li></ul></div>
<div class="abs foot-col" style="left:596px"><h4>Other Links</h4><ul><li>Privacy Policy</li><li>Term &amp; Conditions</li><li>Terms of Services</li></ul></div>
<div class="abs foot-col" style="left:791px"><h4>Contact Details</h4>
  <div class="contact-line"><svg width="12" height="16" viewBox="0 0 12 16" fill="none" stroke="#1f7fcc" stroke-width="1.3"><path d="M6 15S1 9 1 6a5 5 0 0 1 10 0c0 3-5 9-5 9z"/><circle cx="6" cy="6" r="2"/></svg>24A Lorem Ipsum Dolor amet, 4034</div>
  <div class="contact-line"><svg width="13" height="10" viewBox="0 0 13 10" fill="none" stroke="#1f7fcc" stroke-width="1.2"><rect x=".6" y=".6" width="11.8" height="8.8"/><path d="M.6.6l5.9 5 5.9-5"/></svg>info@brightpathconsult.com</div>
  <div class="contact-line"><svg width="13" height="13" viewBox="0 0 11 11" fill="none" stroke="#1f7fcc" stroke-width="1"><path d="M2 .5l2 3-1 1.5q1 2 3 3l1.5-1 3 2L9 10.5Q1 9 .5 2z"/></svg>(1)+888-888-8888</div>
</div>
<div class="abs foot-divider"></div>
<div class="abs copyright">© 2025 BrightPath consult &nbsp;|&nbsp; All Rights Reserved</div>

</body>
</html>
```